New Business Card Design Project LORVANTI-Italy

we are LORVANTI-Italy
our company in the market for 3 years we are luxury cosmetic company and its about time for a facelift :)
i will like to have elegant luxurious and unique business card
that will give the person that get it a unique, luxurious and elegant impression
I'm VERY OPEN FOR NEW IDEAS , even duo i add a few files of things that i see on line and i like them

i add my logo as well
my website is LORVANTI.COM
(if you would like to see the main style that we have)

Target Market(s)

adult that have money :)

Industry/Entity Type

Business

Contact Information for Business Card

Name - Dario Lorvanti
Position - CEO and CO Founder
address - 4817 E Halvern
telephone - 555-384-1926
email - dario@lorvanti.com
fax - 555-384-1926
website - LORVANTI.COM

Colors
000000
959595
fbee3e
ffffff

Requirements
Must have
• big logo in GOLD color
• elegant look
• impressive
Nice to have
• not must but maybe classy pattern background
• not must but maybe emblem
• maybe clear plastic business card
Should not have
• colors
• images

```html
<!DOCTYPE html>
<html lang="en">
<head>
<meta charset="utf-8">
<title>Lorvanti Italy – Business Card</title>
<link rel="stylesheet" href="https://fonts.googleapis.com/css2?family=Exo+2:ital,wght@0,200;0,300;1,200;1,300&display=swap">
<style>
  :root {
    --card-black: #0b0b0b;
    --card-charcoal: #2a2a2a;
    --gold: #e0b43c;
    --gold-soft: #d4a93a;
    --text-white: #ffffff;
    --text-grey: #959595;
    --divider: #f2f2f2;
  }
  * { box-sizing: border-box; margin: 0; padding: 0; }
  html, body {
    width: 1200px;
    height: 760px;
    overflow: hidden;
    background: var(--card-black);
  }
  .card {
    position: relative;
    width: 1200px;
    height: 760px;
    overflow: hidden;
    font-family: "Exo 2", "Helvetica Neue", Arial, sans-serif;
  }
  .card__texture {
    position: absolute;
    inset: 0;
    background:
      radial-gradient(ellipse 70% 65% at 45% 35%, #3a3a3a 0%, var(--card-charcoal) 35%, #141414 80%, var(--card-black) 100%);
  }
  .brand-mark {
    position: absolute;
    left: 186px;
    top: 41px;
    width: 210px;
    height: 210px;
    border-radius: 50%;
    background: var(--gold);
  }
  .brand-name {
    position: absolute;
    left: 40px;
    top: 290px;
    width: 500px;
    text-align: center;
    color: var(--gold);
    font-weight: 300;
    line-height: 1;
  }
  .brand-name__main {
    display: block;
    font-size: 78px;
    letter-spacing: 4px;
  }
  .brand-name__region {
    display: block;
    margin-top: 36px;
    font-size: 30px;
    letter-spacing: 4px;
  }
  .person {
    position: absolute;
    right: 58px;
    top: 60px;
    text-align: right;
  }
  .person__name {
    color: var(--text-white);
    font-weight: 200;
    font-size: 78px;
    letter-spacing: 3px;
    line-height: 1;
  }
  .person__title {
    margin-top: 30px;
    color: var(--gold);
    font-weight: 200;
    font-style: italic;
    font-size: 46px;
    letter-spacing: 2px;
    line-height: 1;
  }
  .contact-divider {
    position: absolute;
    left: 593px;
    top: 416px;
    width: 3px;
    height: 270px;
    background: var(--divider);
  }
  .contact-list {
    position: absolute;
    left: 612px;
    top: 440px;
    list-style: none;
  }
  .contact-list__item {
    display: flex;
    align-items: center;
    height: 62px;
  }
  .contact-list__icon {
    width: 60px;
    display: flex;
    justify-content: center;
    color: var(--gold);
  }
  .contact-list__icon svg { display: block; }
  .contact-list__label {
    font-size: 34px;
    font-style: italic;
    font-weight: 300;
    color: var(--gold);
  }
  .contact-list__value {
    margin-left: 36px;
    color: var(--text-grey);
    font-style: italic;
    font-weight: 300;
    font-size: 43px;
    letter-spacing: 4px;
    line-height: 1;
  }
  .website {
    position: absolute;
    left: 58px;
    top: 682px;
    color: var(--gold);
    font-weight: 300;
    font-size: 45px;
    letter-spacing: 2px;
    line-height: 1;
  }
</style>
</head>
<body>
  <main class="card">
    <div class="card__texture" role="img" aria-label="Dark charcoal background with subtle diagonal pinstripe texture"></div>

    <div class="brand-mark" aria-hidden="true"></div>
    <div class="brand-name">
      <span class="brand-name__main">LORVANTI</span>
      <span class="brand-name__region">ITALY</span>
    </div>

    <header class="person">
      <h1 class="person__name">Dario Lorvanti</h1>
      <p class="person__title">CEO and CO Founder</p>
    </header>

    <div class="contact-divider"></div>
    <ul class="contact-list">
      <li class="contact-list__item">
        <span class="contact-list__icon">
          <svg width="28" height="40" viewBox="0 0 28 40" aria-label="Address">
            <path d="M14 0C6.3 0 0 6.2 0 13.8 0 24 14 40 14 40s14-16 14-26.2C28 6.2 21.7 0 14 0z" fill="currentColor"/>
            <circle cx="14" cy="13.5" r="5" fill="#1a1a1a"/>
          </svg>
        </span>
        <span class="contact-list__value">4817 E Halvern</span>
      </li>
      <li class="contact-list__item">
        <span class="contact-list__icon">
          <svg width="38" height="38" viewBox="0 0 38 38" aria-label="Phone">
            <path d="M8 3l6 8-3.5 3.5c2 4.5 5.5 8 10 10L24 21l8 6-3.5 7C16 33 5 22 4 8z" fill="currentColor"/>
            <path d="M22 6a10 10 0 0 1 10 10M22 1a15 15 0 0 1 15 15" stroke="currentColor" stroke-width="2.5" fill="none"/>
          </svg>
        </span>
        <span class="contact-list__value">555-384-1926</span>
      </li>
      <li class="contact-list__item">
        <span class="contact-list__icon">
          <svg width="40" height="28" viewBox="0 0 40 28" aria-label="Email">
            <rect x="0" y="0" width="40" height="28" fill="currentColor"/>
            <path d="M1 1l19 15L39 1" stroke="#1a1a1a" stroke-width="2.5" fill="none"/>
          </svg>
        </span>
        <span class="contact-list__value">dario@lorvanti.com</span>
      </li>
      <li class="contact-list__item">
        <span class="contact-list__icon"><span class="contact-list__label">fax</span></span>
        <span class="contact-list__value">555-384-1926</span>
      </li>
    </ul>

    <p class="website">Lorvanti.com</p>
  </main>
</body>
</html>
```